Stylish High End Wedding Videography/Films Website (BMRT)

We need a modern and high-end website look for our wedding video and films business. We films weddings all over the United Kingdom and at European destinations so need something to reflect our work. The website should be visually stunning with images and videos being the focal point as this is what our services are;

I have uploads of some items I like and the features the site needs to have. These have been taken from other websites using standout features.

We need the following pages;

1 - Homepage
2 - Films Index Page
3 - Individual Films Page
4 - Prices / Collection Page
5 - Reviews
6 - Options
7 - About
8 - Contact
9 - Blog Index
10 - Blog Page

All pages must be consistent so have a similar style.

Pages on menu:
Films
Prices
Reviews
Options
About
Contact

We require a responsive look too. Over 90% of our visitors access the website via their mobile devices.

Please use the colours from our logo to incorporate into the website.

Target Market(s)

Wedding Couples

Industry/Entity Type

Wedding Photography

Number of Pages Required

5+ page

Font styles to use
Sans Serif
Script

Requirements
Must have
• The logo must be in the centre of the menu at the top.

Social icons at the bottom of the page.

Use only two fonts including Lore which is supplied
Nice to have
• Different video for each page on the top header. This will play behind the menu.

```html
<!DOCTYPE html>
<html lang="en">
<head>
<meta charset="utf-8">
<title>BMRT Wedding Films – Portfolio</title>
<link rel="stylesheet" href="https://fonts.googleapis.com/css2?family=Montserrat:wght@400;500;600;700&family=Poppins:wght@500;600;700&display=swap">
<style>
:root{
  --gold:#a38b55;
  --gold-deep:#9a8049;
  --ink:#3b332c;
  --muted:#7a7570;
  --footer:#4a3e36;
  --button:#4b4036;
  --white:#ffffff;
}
*{margin:0;padding:0;box-sizing:border-box}
html,body{width:1200px;height:3425px;overflow:hidden;background:var(--white)}
body{font-family:"Montserrat",sans-serif;color:var(--ink);position:relative}
.page{position:relative;width:1200px;height:3425px;overflow:hidden}

/* Hero */
.hero{position:absolute;left:0;top:0;width:1200px;height:459px;
  background:linear-gradient(180deg,#5d6468 0%,#3f4a3c 32%,#6d7a48 55%,#8e8a5e 78%,#6b5f4a 100%)}
.hero::after{content:"";position:absolute;inset:0;background:linear-gradient(180deg,rgba(0,0,0,.25),rgba(0,0,0,.05) 50%,rgba(0,0,0,.2))}
.nav{position:absolute;top:82px;font-size:13px;color:var(--white);display:flex;align-items:center;z-index:2;letter-spacing:.2px}
.nav a{color:inherit;text-decoration:none}
.nav .dot{width:4px;height:4px;border-radius:50%;background:var(--white);margin:0 19px}
.nav .active{color:var(--gold)}
.nav-left{left:227px}
.nav-right{left:764px}
.brand{position:absolute;left:0;width:1200px;top:18px;text-align:center;z-index:2;color:var(--white)}
.brand-mark{width:30px;height:30px;border-radius:50%;background:var(--gold);margin:0 auto 16px}
.brand-name{font-family:"Montserrat",sans-serif;font-weight:600;font-size:20px;letter-spacing:6px}
.hero-title{position:absolute;left:153px;top:318px;z-index:2;font-family:"Poppins",sans-serif;font-weight:600;font-size:54px;color:transparent;-webkit-text-stroke:1.2px var(--white);letter-spacing:1px}
.hero-sub{position:absolute;left:153px;top:392px;z-index:2;font-family:"Poppins",sans-serif;font-weight:700;font-size:17px;color:var(--white)}

/* Film list */
.film{position:absolute;left:267px;width:666px;height:344px}
.film.featured{box-shadow:0 18px 40px rgba(0,0,0,.16)}
.film-still{position:absolute;inset:0}
.play{position:absolute;left:287px;top:126px;width:92px;height:92px;border-radius:50%;background:rgba(255,255,255,.22)}
.play svg{position:absolute;left:30px;top:28px}
.film-label{position:absolute;left:186px;width:50px;display:flex;writing-mode:vertical-rl;transform:rotate(180deg);align-items:flex-start;gap:8px}
.film-title{font-family:"Poppins",sans-serif;font-weight:700;font-size:18px;color:var(--ink);white-space:nowrap}
.film-title .num{color:var(--gold);margin-bottom:30px}
.film-title.is-active{color:var(--gold)}
.film-venue{font-size:11.5px;color:var(--muted);white-space:nowrap;margin-top:0}

.link-line{position:absolute;display:flex;align-items:center;font-size:11px;font-weight:600;letter-spacing:2.6px;color:var(--ink)}
.link-line::before{content:"";width:2px;height:16px;background:var(--gold);margin-right:14px}

/* Feature */
.feature-media{position:absolute;left:153px;top:2645px;width:448px;height:281px;
  background:linear-gradient(160deg,#8a8276 0%,#9a7d5c 45%,#6e5a44 75%,#7a3f33 100%)}
.feature-heading{position:absolute;left:677px;top:2682px;width:320px;font-family:"Poppins",sans-serif;font-weight:600;font-size:28px;line-height:36px;color:var(--ink)}
.feature-text{position:absolute;left:677px;top:2767px;width:345px;font-size:12.5px;line-height:20px;color:var(--muted)}

/* CTA band */
.cta{position:absolute;left:0;top:3018px;width:1200px;height:153px;background:var(--gold)}
.cta-text{position:absolute;left:292px;top:56px;font-family:"Poppins",sans-serif;font-weight:600;font-size:27px;color:var(--ink)}
.cta-button{position:absolute;left:690px;top:51px;width:190px;height:49px;background:var(--button);color:var(--gold);font-size:12.5px;font-weight:600;display:flex;align-items:center;justify-content:center}

/* Footer */
.footer{position:absolute;left:0;top:3171px;width:1200px;height:254px;background:var(--footer);color:var(--white)}
.footer-brand{position:absolute;left:153px;top:88px;display:flex;align-items:center;gap:12px;font-family:"Montserrat",sans-serif;font-weight:600;font-size:28px;letter-spacing:3px;color:var(--gold)}
.footer-brand span.sq{width:14px;height:14px;background:var(--gold)}
.footer-col{position:absolute;top:69px}
.footer-col h4{font-size:12.5px;font-weight:600;letter-spacing:2.6px;margin-bottom:14px}
.footer-col .big{font-size:19px;margin-bottom:6px}
.footer-col .big em{font-style:normal;color:var(--gold)}
.footer-col .small{font-size:12px}
.badge{position:absolute;left:987px;top:73px;width:54px;height:54px;border-radius:50%;background:#efe08a;border:2px solid #d8c766}
.to-top{position:absolute;left:1152px;top:72px}
.footer-rule{position:absolute;left:77px;top:191px;width:1046px;height:1px;background:rgba(255,255,255,.18)}
.copyright{position:absolute;left:153px;top:216px;font-size:10.5px;color:rgba(255,255,255,.85)}
.social{position:absolute;top:207px;width:30px;height:30px;border-radius:50%;background:rgba(255,255,255,.14)}
</style>
</head>
<body>
<div class="page">

  <header class="hero">
    <div class="hero-photo" role="img" aria-label="Bride and groom kissing in a meadow as guests throw confetti"></div>
    <nav class="nav nav-left"><a class="active">Films</a><span class="dot"></span><a>Prices</a><span class="dot"></span><a>Reviews</a></nav>
    <div class="brand"><div class="brand-mark"></div><div class="brand-name">BMRT</div></div>
    <nav class="nav nav-right"><a>Options</a><span class="dot"></span><a>About</a><span class="dot"></span><a>Contact</a></nav>
    <h1 class="hero-title">Wedding Film</h1>
    <p class="hero-sub">Portfolio</p>
  </header>

  <!-- 01 -->
  <article class="film featured" style="top:542px">
    <div class="film-still" role="img" aria-label="Couple walking through guests throwing petals" style="background:linear-gradient(150deg,#9aa0a0 0%,#6d6a5e 40%,#4f5a4c 70%,#8b8a80 100%)"></div>
    <div class="play"><svg width="36" height="36" viewBox="0 0 36 36"><path d="M6 3 L32 18 L6 33 Z" fill="none" stroke="#fff" stroke-width="2.4"/></svg></div>
  </article>
  <div class="film-label" style="top:542px;height:344px;justify-content:flex-start">
    <div class="film-title is-active"><span class="num">01.</span>Hattie &amp; Owen</div>
    <div class="film-venue">Larkmoor Hall, Northumberland</div>
  </div>

  <!-- 02 -->
  <article class="film" style="top:933px">
    <div class="film-still" role="img" aria-label="Couple embracing beside a white bouquet" style="background:linear-gradient(120deg,#c9c6a4 0%,#8ea06a 30%,#2f4a78 55%,#d9b090 80%,#ece6df 100%)"></div>
    <div class="play"><svg width="36" height="36" viewBox="0 0 36 36"><path d="M6 3 L32 18 L6 33 Z" fill="none" stroke="#fff" stroke-width="2.4"/></svg></div>
  </article>
  <div class="film-label" style="top:933px;height:344px">
    <div class="film-title"><span class="num">02.</span>Rosa &amp; Finn</div>
    <div class="film-venue">Fernbrook Acres, Northumberland</div>
  </div>

  <!-- 03 -->
  <article class="film" style="top:1322px">
    <div class="film-still" role="img" aria-label="Couple celebrating on a hillside among flying petals" style="background:linear-gradient(170deg,#c7c4bd 0%,#a79a86 40%,#8b6d4f 70%,#7c4a3a 100%)"></div>
    <div class="play"><svg width="36" height="36" viewBox="0 0 36 36"><path d="M6 3 L32 18 L6 33 Z" fill="none" stroke="#fff" stroke-width="2.4"/></svg></div>
  </article>
  <div class="film-label" style="top:1322px;height:344px">
    <div class="film-title"><span class="num">03.</span>Imani &amp; Theo</div>
    <div class="film-venue">Villa Castellaro, Liguria, Italy</div>
  </div>

  <!-- 04 -->
  <article class="film" style="top:1711px">
    <div class="film-still" role="img" aria-label="Laughing couple in front of a yellow villa" style="background:linear-gradient(110deg,#6f8c7a 0%,#4f6a55 30%,#e0b24a 55%,#d59a3c 75%,#c9d0d8 100%)"></div>
    <div class="play"><svg width="36" height="36" viewBox="0 0 36 36"><path d="M6 3 L32 18 L6 33 Z" fill="none" stroke="#fff" stroke-width="2.4"/></svg></div>
  </article>
  <div class="film-label" style="top:1711px;height:344px">
    <div class="film-title"><span class="num">04.</span>Nell &amp; Callum</div>
    <div class="film-venue">Ashcombe Manor, Leicestershire</div>
  </div>

  <!-- 05 -->
  <article class="film" style="top:2101px">
    <div class="film-still" role="img" aria-label="Couple leaving a church under falling petals" style="background:linear-gradient(100deg,#8a6a5c 0%,#5a4640 30%,#2d3344 55%,#3a3230 80%,#6a5a55 100%)"></div>
    <div class="play"><svg width="36" height="36" viewBox="0 0 36 36"><path d="M6 3 L32 18 L6 33 Z" fill="none" stroke="#fff" stroke-width="2.4"/></svg></div>
  </article>
  <div class="film-label" style="top:2101px;height:344px">
    <div class="film-title"><span class="num">05.</span>Ivy &amp; Marcus</div>
    <div class="film-venue">The Old Drover, Durham</div>
  </div>

  <a class="link-line" style="left:549px;top:2536px">LOAD MORE</a>

  <section>
    <div class="feature-media" role="img" aria-label="Couple celebrating on a hillside among flying petals"></div>
    <div class="play" style="left:331px;top:2740px"><svg width="36" height="36" viewBox="0 0 36 36"><path d="M6 3 L32 18 L6 33 Z" fill="none" stroke="#fff" stroke-width="2.4"/></svg></div>
    <h2 class="feature-heading">Want Something a More Funky?</h2>
    <p class="feature-text">If you are a couple who prefers something a bit different to the styles above then why not go for our alternative option.</p>
    <a class="link-line" style="left:679px;top:2867px">SEND US MESSAGE</a>
  </section>

  <section class="cta">
    <p class="cta-text">Start your project with us</p>
    <a class="cta-button">Get Started Now!</a>
  </section>

  <footer class="footer">
    <div class="footer-brand"><span class="sq"></span>BMRT</div>
    <div class="footer-col" style="left:344px">
      <h4>CONTACT US</h4>
      <p class="big">Call. <em>+44 7700 900123</em></p>
      <p class="small">e. films@bmrtfilms.com</p>
    </div>
    <div class="footer-col" style="left:677px">
      <h4>GET IN TOUCH</h4>
      <p class="big">NE4 2XY Harwick</p>
      <p class="small">Elmsford Vale United Kingdom</p>
    </div>
    <div class="badge" role="img" aria-label="Featured listing badge"></div>
    <svg class="to-top" width="20" height="22" viewBox="0 0 20 22"><path d="M10 21 V2 M3 9 L10 2 L17 9" fill="none" stroke="#a38b55" stroke-width="1.6"/></svg>
    <div class="footer-rule"></div>
    <p class="copyright">2020 © BMRT Wedding Films. All Rights Reserved.</p>
    <span class="social" style="left:940px" aria-label="Social link 1"></span>
    <span class="social" style="left:979px" aria-label="Social link 2"></span>
    <span class="social" style="left:1018px" aria-label="Social link 3"></span>
  </footer>

</div>
</body>
</html>
```